BRAMBLEFORD CONSTRUCTIONS B-Card

I currently have a b-card design but will be removing the image (tree) from the logo and have text only.
I want the card to be classy and strong within the building and construction industry.
I will be using Spot UV on the cards as per the attached examples. I will also send through some sketched ideas that I have in mind.
The color blue is similar to the image (No. 6) attached images

Target Market(s)

middle to maturre aged.
Home Owners / Renovators and Builders

Industry/Entity Type

Construction

Contact Information for Business Card

BRAMBLEFORD CONSTRUCTIONS
Name: Gareth Pennick
Title: Project Manager
Mobile: 0427 351 804
Office: (08) 9316 5172
Address: 47C Corvell Street, Malaga WA 6090
Email: info@bramblefordhomes.com.au
PO Box: 3817 Ashvale WA 6972

Colors
0592cd
33a6d7
85cae6
1b1b1b

Requirements
Must have
• 1. It must have spot UV on the front of card, maybe back of card too
• 2. I really like the blue on image 6. (or at least a really cool electric blue against the charcoal grey background)
• 3. The font must be slimline and modern. Easy to read
• 4. There must be no black used on the card... Only greys and dark charcoal greys
• 5. Use only the text from the logo "Brambleford Constructions" Not the image of the tree. I am wanting the b-cards to be more masculine.
Nice to have
• 1. I like the design concept on image 6. but happy to see what else you can do with the Spot UV
• 2. Unless you have a really cool idea of the image of the tree (from previous logo) Spot UV somewhere in the design concept thats original and different then I am keen to see what you come up with
• 3. Try changing the color of the logo eg. full white or Blue and white
• 4. Another option is to have the Brambleford Logo on the front of card with the spot UV in the background of text which we specialise in eg, Roofing, Ceiling, Insulation, Gutter Guards, Electrical, Insurance etc and we can add or reduce items as required. Similar to image 12.
Should not have
• Do not include the image of the tree from previous logo. unless you have a really cool idea of Spot UV somewhere in the design concept thats original and different.

```html
<!DOCTYPE html>
<html lang="en">
<head>
<meta charset="utf-8">
<title>Brambleford Constructions – Business Card</title>
<link rel="stylesheet" href="https://fonts.googleapis.com/css2?family=Jost:wght@400;500;600&display=swap">
<style>
  :root {
    --brand-blue: #1d5eaa;
    --card-blue: #1c5fac;
    --pattern-light: #3f7cc4;
    --text-grey: #4a4a4a;
    --paper: #ffffff;
    --backdrop: #e6e6e6;
  }
  * { box-sizing: border-box; margin: 0; padding: 0; }
  html, body { width: 1200px; height: 987px; overflow: hidden; }
  body { background: var(--backdrop); font-family: "Jost", sans-serif; position: relative; }

  .card { position: absolute; left: 299px; width: 611px; height: 348px; box-shadow: 0 2px 6px rgba(0,0,0,.25); overflow: hidden; }
  .card--front { top: 157px; background: var(--paper); }
  .card--back { top: 527px; background: var(--card-blue); }

  .brand { position: absolute; left: 39px; top: 72px; color: var(--brand-blue); font-weight: 500; font-size: 30px; line-height: 1; white-space: nowrap; }

  .rule { position: absolute; top: 177px; left: 0; width: 611px; height: 3px; background: var(--brand-blue); }
  .name-band { position: absolute; top: 177px; left: 0; width: 284px; height: 61px; background: var(--brand-blue); clip-path: polygon(0 0, 100% 0, 84% 100%, 0 100%); }
  .person { position: absolute; left: 37px; top: 183px; color: #fff; }
  .person__name { font-size: 23px; font-weight: 600; line-height: 1.15; }
  .person__title { font-size: 17px; font-weight: 400; line-height: 1.2; }

  .address { position: absolute; left: 39px; top: 256px; color: var(--text-grey); font-size: 16.5px; line-height: 22px; font-style: normal; }
  .contacts { position: absolute; right: 32px; top: 225px; list-style: none; color: var(--text-grey); font-size: 16.5px; line-height: 23.5px; text-align: right; }
  .contacts li { display: flex; align-items: center; justify-content: flex-end; gap: 10px; }
  .contacts .email, .contacts .web { font-size: 15px; }
  .icon { width: 15px; height: 15px; fill: var(--brand-blue); flex: none; }

  .service-pattern { position: absolute; inset: 0; background: linear-gradient(135deg, var(--pattern-light) 0%, var(--card-blue) 55%, var(--pattern-light) 100%); }
  .back-brand { position: absolute; left: 240px; top: 140px; width: 330px; padding: 10px 14px; background: var(--card-blue); color: #fff; font-weight: 500; font-size: 21px; line-height: 1.2; text-align: center; white-space: nowrap; }
</style>
</head>
<body>

<section class="card card--front" aria-label="Business card front">
  <p class="brand">Brambleford Constructions</p>
  <div class="rule"></div>
  <div class="name-band"></div>
  <div class="person">
    <p class="person__name">Gareth Pennick</p>
    <p class="person__title">Project Manager</p>
  </div>
  <address class="address">
    47C Corvell Street<br>
    Ashvale WA 6071<br>
    PO Box: 3817 Ashvale WA 6972
  </address>
  <ul class="contacts">
    <li>(08) 9316 5172
      <svg class="icon" viewBox="0 0 24 24" aria-hidden="true"><path d="M6.6 10.8a15 15 0 0 0 6.6 6.6l2.2-2.2a1 1 0 0 1 1-.25 11.4 11.4 0 0 0 3.6.57 1 1 0 0 1 1 1V20a1 1 0 0 1-1 1A17 17 0 0 1 3 4a1 1 0 0 1 1-1h3.5a1 1 0 0 1 1 1c0 1.25.2 2.45.57 3.6a1 1 0 0 1-.25 1z"/></svg></li>
    <li>0427 351 804
      <svg class="icon" viewBox="0 0 24 24" aria-hidden="true"><path d="M7 1h10a2 2 0 0 1 2 2v18a2 2 0 0 1-2 2H7a2 2 0 0 1-2-2V3a2 2 0 0 1 2-2zm0 3v15h10V4z"/></svg></li>
    <li class="email">info@bramblefordhomes.com.au
      <svg class="icon" viewBox="0 0 24 24" aria-hidden="true"><path d="M2 5h20v14H2zm2 2v.5l8 5 8-5V7l-8 5z"/></svg></li>
    <li class="web">bramblefordhomes.com.au
      <svg class="icon" viewBox="0 0 24 24" aria-hidden="true"><path d="M12 2a10 10 0 1 0 0 20 10 10 0 0 0 0-20zm-1 17.9A8 8 0 0 1 4.2 10L9 14.8v1.2a2 2 0 0 0 2 2zm6.9-2.5A2 2 0 0 0 16 16h-1v-3a1 1 0 0 0-1-1H8v-2h2a1 1 0 0 0 1-1V7h2a2 2 0 0 0 2-2v-.4a8 8 0 0 1 2.9 12.8z"/></svg></li>
  </ul>
</section>

<section class="card card--back" aria-label="Business card back">
  <div class="service-pattern" role="img" aria-label="Spot UV background pattern of the trade services offered"></div>
  <p class="back-brand">Brambleford Constructions</p>
</section>

</body>
</html>
```